Bramblecrest Resource Group is a recycling company. We have started a marketing campaign and would love your artwork to help us get started. We would like the fallowing to be on our postcard:
At the top please write: Now servicing businesses in the city of Industry!
Below that we would like 3 pictures.. The first is a picture of trash, the second is a our logo and at plus sign. After that would be a picture of neat baled recycled material and the last picture would be money. Below this please right the following:
- Companies choose bramblecrest resource group because:
- if it can be recycled we will find a use for it
- we pay top dollar
- starting our service is fast and easy
* All it takes is one call/email and we will handle the rest
At the bottom please put our contact information
- 800.514.2976
- delphine@bramble722.com
- bramble722.com

Thanks guys! I have attached our logo!

I am sorry for this late post,but could you not put anything on the back except for a return address which is 4187 Tillery Ave Costa Mesa, Ca 92871 Thank you! We have had a lot of trouble in the past with the post office when we put stuff on the back for some reason.

Recycling

```html
<!DOCTYPE html>
<html lang="en">
<head>
<meta charset="utf-8">
<title>Bramblecrest Resource Group – Postcard</title>
<link rel="stylesheet" href="https://fonts.googleapis.com/css2?family=Open+Sans:wght@300;400;600&family=Roboto+Condensed:wght@300;400&display=swap">
<style>
  :root {
    --green: #6db33f;
    --green-deep: #2f7a1c;
    --green-mid: #58a23a;
    --green-pale: #d9ecc9;
    --ink: #4f4f4a;
    --ink-dark: #2e2e2b;
    --rule: rgba(70, 70, 65, 0.55);
    --panel: rgba(235, 240, 230, 0.55);
    --bar: rgba(255, 255, 255, 0.28);
    --white: #ffffff;
  }
  * { box-sizing: border-box; margin: 0; padding: 0; }
  html, body { width: 1200px; height: 776px; overflow: hidden; background: #fff; }
  .postcard {
    position: relative;
    width: 1200px; height: 776px;
    overflow: hidden;
    font-family: "Open Sans", Arial, sans-serif;
    background:
      radial-gradient(ellipse 900px 620px at 690px 40px, #ffffff 0%, #e6f3dc 22%, #a9d68a 48%, #5faf3d 72%, #2f7d20 100%);
  }
  .side-panel {
    position: absolute; left: 0; top: 0;
    width: 372px; height: 776px;
    background: var(--panel);
  }
  .rule { position: absolute; left: 0; height: 2px; background: var(--rule); }
  .rule--top { top: 234px; width: 930px; }
  .rule--mid { top: 452px; width: 372px; }

  .brand {
    position: absolute; left: 0; top: 40px; width: 372px;
    display: flex; flex-direction: column; align-items: center; gap: 14px;
  }
  .brand__dot { width: 60px; height: 60px; border-radius: 50%; background: var(--green); }
  .brand__name {
    font-weight: 600; font-size: 30px; line-height: 1.1;
    color: var(--ink); text-align: center;
  }

  .service-area {
    position: absolute; left: 0; top: 250px; width: 372px;
    text-align: center; font-weight: 400; font-size: 30px; line-height: 47px;
    color: var(--ink);
  }
  .service-area .accent { color: var(--green); }

  .contact { position: absolute; left: 0; width: 372px; text-align: center; }
  .contact__icon {
    display: block; margin: 0 auto 6px;
    width: 32px; height: 32px; border-radius: 50%;
    background: #f4f4f2; box-shadow: 0 1px 3px rgba(0,0,0,0.35);
  }
  .contact__text {
    font-size: 17px; letter-spacing: 1.6px; color: var(--ink-dark);
  }
  .contact--phone { top: 497px; }
  .contact--email { top: 586px; }
  .contact--web { top: 677px; }

  .headline {
    position: absolute; left: 410px; top: 58px;
    font-size: 27px; line-height: 35px; color: var(--ink);
  }
  .headline .accent { color: var(--green); }

  .reason {
    position: absolute; left: 396px;
    padding: 6px 14px;
    background: var(--bar);
    font-family: "Roboto Condensed", "Arial Narrow", sans-serif;
    font-weight: 300; font-size: 28px; line-height: 34px; color: var(--ink);
  }
  .reason--recycle { top: 296px; }
  .reason--pay { top: 394px; }
  .reason--start { top: 492px; }
  .reason--call {
    top: 628px; padding: 10px 14px;
    font-weight: 400; font-size: 30px; line-height: 36px; color: var(--white);
    background: rgba(255, 255, 255, 0.16);
  }

  .step {
    position: absolute; left: 930px;
    width: 230px; height: 230px; border-radius: 50%;
    background: var(--white);
    box-shadow: 0 2px 8px rgba(0,0,0,0.35);
    overflow: hidden;
  }
  .step--bin { top: 20px; }
  .step--materials { top: 270px; }
  .step--money { top: 524px; }
  .step__art { position: absolute; }
  .art-bin {
    left: 75px; top: 18px; width: 82px; height: 194px; border-radius: 10px;
    background: linear-gradient(90deg, #1f6b1f, #3f9c3a 45%, #1d5e1b);
  }
  .art-materials {
    left: 40px; top: 30px; width: 150px; height: 62px; border-radius: 8px;
    background: linear-gradient(180deg, #c9c9c4, #8f8e86);
  }
  .plus {
    position: absolute; left: 101px; top: 100px;
    font-size: 40px; font-weight: 300; color: var(--ink); line-height: 1;
  }
  .step__name {
    position: absolute; left: 0; top: 158px; width: 230px; text-align: center;
    font-weight: 600; font-size: 17px; color: var(--ink);
  }
  .art-money {
    left: 24px; top: 48px; width: 184px; height: 140px; border-radius: 8px;
    background: linear-gradient(160deg, #dfe6d7, #8d9d82 60%, #6d7c63);
  }
  .connector { position: absolute; left: 1039px; width: 12px; height: 12px; }
  .connector--one { top: 259px; }
  .connector--two { top: 512px; }
</style>
</head>
<body>
<main class="postcard">
  <div class="side-panel"></div>
  <div class="rule rule--top"></div>
  <div class="rule rule--mid"></div>

  <header class="brand">
    <span class="brand__dot"></span>
    <p class="brand__name">Bramblecrest<br>Resource Group</p>
  </header>

  <p class="service-area">
    <span class="accent">Now servicing</span><br>
    businesses<br>
    in the city of<br>
    <span class="accent">Industry!</span>
  </p>

  <div class="contact contact--phone">
    <svg class="contact__icon" viewBox="0 0 32 32" aria-hidden="true">
      <circle cx="16" cy="16" r="16" fill="#f4f4f2"/>
      <path d="M11 9c1-.6 2 0 2.6 1l1.2 2.2c.4.8.2 1.6-.5 2.1l-.8.6c.7 1.8 2 3.2 3.7 4l.7-.8c.6-.6 1.4-.8 2.1-.4l2.2 1.2c1 .6 1.4 1.6.8 2.6-.9 1.4-2.3 2-3.9 1.6-4.6-1.2-8.2-4.8-9.4-9.4-.4-1.6.2-3 1.3-3.5z" fill="#5a5a55"/>
    </svg>
    <p class="contact__text">800.514.2976</p>
  </div>
  <div class="contact contact--email">
    <svg class="contact__icon" viewBox="0 0 32 32" aria-hidden="true">
      <circle cx="16" cy="16" r="16" fill="#f4f4f2"/>
      <text x="16" y="22" text-anchor="middle" font-family="Open Sans, sans-serif" font-size="17" font-weight="600" fill="#5a5a55">@</text>
    </svg>
    <p class="contact__text">DELPHINE@BRAMBLE722.COM</p>
  </div>
  <div class="contact contact--web">
    <svg class="contact__icon" viewBox="0 0 32 32" aria-hidden="true">
      <circle cx="16" cy="16" r="16" fill="#f4f4f2"/>
      <g fill="none" stroke="#5a5a55" stroke-width="1.5">
        <circle cx="16" cy="16" r="8"/>
        <ellipse cx="16" cy="16" rx="3.6" ry="8"/>
        <line x1="8" y1="16" x2="24" y2="16"/>
        <path d="M9.5 11.5h13M9.5 20.5h13"/>
      </g>
    </svg>
    <p class="contact__text">BRAMBLE722.COM</p>
  </div>

  <h1 class="headline" style="font-weight:400">
    Companies choose<br>
    Bramblecrest <span class="accent">Resource</span> Group<br>
    because:
  </h1>

  <p class="reason reason--recycle">if it can be recycled we will find a use for it</p>
  <p class="reason reason--pay">we pay top dollar</p>
  <p class="reason reason--start">starting our service is fast and easy</p>
  <p class="reason reason--call">All it takes is one call/email<br>and we will handle the rest</p>

  <div class="step step--bin">
    <div class="step__art art-bin" role="img" aria-label="Green recycling bin"></div>
  </div>
  <svg class="connector connector--one" viewBox="0 0 12 12" aria-hidden="true">
    <circle cx="6" cy="6" r="5.5" fill="none" stroke="#6db33f"/>
    <path d="M3.5 5l2.5 2.5L8.5 5" fill="none" stroke="#6db33f"/>
  </svg>
  <div class="step step--materials">
    <div class="step__art art-materials" role="img" aria-label="Pile of recyclable bottles, cans and cardboard"></div>
    <span class="plus">+</span>
    <p class="step__name">Bramblecrest</p>
  </div>
  <svg class="connector connector--two" viewBox="0 0 12 12" aria-hidden="true">
    <circle cx="6" cy="6" r="5.5" fill="none" stroke="#6db33f"/>
    <path d="M3.5 5l2.5 2.5L8.5 5" fill="none" stroke="#6db33f"/>
  </svg>
  <div class="step step--money">
    <div class="step__art art-money" role="img" aria-label="Stacks of banded cash"></div>
  </div>
</main>
</body>
</html>
```